Crestline Plaque & Medal Unique Business Card Design

Recently selected a new logo design and waiting to recieve print files. I've attached image for your review. We are a trophies and awards company that provides engraving on trophies, plaques, name plates, name tags, desk sets, medals, acrylics, and signage.

We are located in Monroe, Louisiana and provide this service with computerized & laser engraving equipment.

Target Market(s)

Corporate, Sport, Church, and Special Events

Industry/Entity Type

Business

Contact Information for Business Card

I'd like to see the following list on the card: Trophies, Plaques, Name Plates, Name Tags, Desk Sets, Medals, Certificates... this is accomplished with Computerized & Laser Engraving

Colors
0555a3
ec1f27
ffffff

Requirements
Must have
• I like either single or double sided. If a design can be created with a frosted card stock I'd consider single. Must be Red, White, and Blue. Dwight Palmer - Owner, 412 W 8th Ave, Monroe, La 71208 office 318-555-0148 fax 318-555-0163 email: info@crestlineplaquemedal.example, and website: www.crestlineplaquemedal.example

```html
<!DOCTYPE html>
<html lang="en">
<head>
<meta charset="utf-8">
<title>Crestline Plaque &amp; Medal – Business Card</title>
<link rel="stylesheet" href="https://fonts.googleapis.com/css2?family=Great+Vibes&family=Questrial&display=swap">
<style>
  :root {
    --page-bg: #e9e6e1;
    --frost-top: #f4f3f1;
    --frost-bottom: #e6e9ef;
    --brand-blue: #0555a3;
    --navy-light: #3c4f96;
    --navy-dark: #1b2768;
    --rule-blue: #1f2f7a;
    --accent-red: #ec1f27;
    --card-text: #eef1f8;
  }
  * { margin: 0; padding: 0; box-sizing: border-box; }
  html, body {
    width: 1200px; height: 970px; overflow: hidden;
    background: var(--page-bg);
    font-family: "Questrial", "Century Gothic", sans-serif;
  }
  .canvas { position: relative; width: 1200px; height: 970px; }
  .business-card {
    position: absolute; left: 60px; top: 185px;
    width: 1080px; height: 600px;
    background: linear-gradient(180deg, var(--frost-top), var(--frost-bottom));
    box-shadow: 0 10px 30px rgba(0,0,0,.18);
    overflow: hidden;
  }
  .brand-area {
    position: absolute; left: 0; top: 0; width: 100%; height: 240px;
    display: flex; align-items: center; justify-content: center; gap: 18px;
  }
  .brand-dot { width: 26px; height: 26px; border-radius: 50%; background: var(--brand-blue); }
  .brand-name { font-size: 56px; color: var(--brand-blue); letter-spacing: .5px; }
  .rule { position: absolute; left: 0; top: 240px; width: 100%; height: 4px; background: var(--rule-blue); }
  .info-band {
    position: absolute; left: 0; top: 250px; width: 100%; height: 350px;
    background: linear-gradient(90deg, var(--navy-light) 0%, #34468d 35%, var(--navy-dark) 62%, var(--navy-dark) 100%);
    color: var(--card-text);
  }
  .contact-column { position: absolute; left: 62px; top: 18px; }
  .person-name { font-family: "Great Vibes", cursive; font-size: 50px; color: var(--accent-red); line-height: 1.1; }
  .person-title { font-size: 22px; margin-top: 6px; }
  .contact-list { list-style: none; margin-top: 38px; }
  .contact-list li { display: flex; align-items: flex-start; gap: 22px; font-size: 27px; line-height: 26px; margin-bottom: 9px; }
  .contact-list svg { width: 26px; height: 26px; flex: none; fill: var(--card-text); }
  .services-column { position: absolute; left: 695px; top: 32px; }
  .services-heading { font-family: "Great Vibes", cursive; font-size: 36px; color: var(--accent-red); }
  .services-list { list-style: none; margin-top: 22px; }
  .services-list li { font-size: 27px; line-height: 31px; }
  .services-list li::before { content: "★"; font-size: 18px; margin-right: 16px; vertical-align: 2px; }
</style>
</head>
<body>
<main class="canvas">
  <section class="business-card">
    <header class="brand-area">
      <span class="brand-dot"></span>
      <span class="brand-name">Crestline Plaque &amp; Medal</span>
    </header>
    <div class="rule"></div>
    <div class="info-band">
      <div class="contact-column">
        <p class="person-name">Dwight Palmer</p>
        <p class="person-title">Managing Director</p>
        <ul class="contact-list">
          <li>
            <svg viewBox="0 0 24 24"><path d="M6.6 10.8a15.1 15.1 0 0 0 6.6 6.6l2.2-2.2a1 1 0 0 1 1-.25 11.4 11.4 0 0 0 3.6.57 1 1 0 0 1 1 1V20a1 1 0 0 1-1 1A17 17 0 0 1 3 4a1 1 0 0 1 1-1h3.5a1 1 0 0 1 1 1c0 1.25.2 2.45.57 3.57a1 1 0 0 1-.25 1z"/></svg>
            <span>318-555-0148</span>
          </li>
          <li>
            <svg viewBox="0 0 24 24"><path d="M2 6h20v12H2z M3.5 7.5l8.5 6 8.5-6" fill="none" stroke="#eef1f8" stroke-width="1.8"/></svg>
            <span>info@crestlineplaquemedal.example</span>
          </li>
          <li>
            <svg viewBox="0 0 24 24"><circle cx="12" cy="12" r="9.5" fill="none" stroke="#eef1f8" stroke-width="1.8"/><path d="M2.5 12h19M12 2.5c3 3 3 16 0 19M12 2.5c-3 3-3 16 0 19" fill="none" stroke="#eef1f8" stroke-width="1.5"/></svg>
            <span>www.crestlineplaquemedal.example</span>
          </li>
          <li>
            <svg viewBox="0 0 24 24"><path d="M12 1.5a7 7 0 0 0-7 7c0 5.3 7 14 7 14s7-8.7 7-14a7 7 0 0 0-7-7zm0 9.7a2.7 2.7 0 1 1 0-5.4 2.7 2.7 0 0 1 0 5.4z"/></svg>
            <span>412 W 8th Ave<br>Monroe, La 71208</span>
          </li>
        </ul>
      </div>
      <div class="services-column">
        <p class="services-heading">Services</p>
        <ul class="services-list">
          <li>engraving on trophies</li>
          <li>plaques</li>
          <li>name plates</li>
          <li>name tags</li>
          <li>desk sets</li>
          <li>medals</li>
          <li>acrylics, and signage</li>
        </ul>
      </div>
    </div>
  </section>
</main>
</body>
</html>
```